International Clinical Software Company needs a new business card design

We are looking for a new business card design for our company that has recently expanded into the UK market, making us a multinational company.
After having rebranded our website and produced a new style guide, we are looking for a business card that is creative and attention grabbing, while being consistent with the style and colour scheme used on the new website, www.plumvora.example
We produce care management technology for the aged care market, but the main aspect we aim to communicate is the human element of our software, and the way it assists in providing better care for aged people, and stronger relationships between aged people and the staff that care for them.
Our current business card is a dark green with gold text, which makes the text quite difficult to read, not very aesthetically appealing and the colour scheme looks quite dated.
We would like something fresh and modern, that can still be colourful but doesn't use large blocks of dark colour, and uses the colours within our logo.
Something tying in with the leaves that are used in our logo could work quite nicely, along with the Autumn/Fall colours of soft greens, yellows and reds (also in our existing logo). However also happy to look at fresh, completely out of the box ideas we may not have yet considered.
Target Market(s)
The people that receive this business card work in the aged card or health industry and are either corporate/management level staff or clinical (Registered Nurses, care workers etc.)
Industry/Entity Type
Health Product
Contact Information for Business Card
Company Name - BrindlewayCare
Company locations: United Kingdom, Australia, New Zealand
Staff Details:
Staff name: Derek Mallow
Staff job title: Executive Chairman
Staff email: d.mallow@plumvora.example
Office phone number: 01742 918576
Font styles to use
Other font styles liked:
- Calibri
Requirements
Must have
- Must include the BrindlewayCare brand name in it's current font
- Must include logo (3 leaves in gold circle)
- Must include Business Card Details
Nice to have
- Elements of gold
- White space
- Something autumn themed but not too cliched
Should not have
- No blue - used by a major competitor and we would like to differentiate from them
- Large blocks of dark green colour (the green that appears in our leaves on the logo on our current business card is the background colour and it is far too dark)

```html
<!DOCTYPE html>
<html lang="en">
<head>
<meta charset="utf-8">
<title>BrindlewayCare – Business Card</title>
<link rel="stylesheet" href="https://fonts.googleapis.com/css2?family=Carlito:wght@400;700&display=swap">
<style>
  :root {
    --backdrop: #e4e4e2;
    --card: #f4f4f3;
    --gold: #9d8a5c;
    --crimson: #a3164b;
    --ink: #555659;
    --rule: #d3d2ce;
    --font: "Carlito", "Calibri", sans-serif;
  }
  * { box-sizing: border-box; margin: 0; padding: 0; }
  html, body {
    width: 1105px;
    height: 1200px;
    overflow: hidden;
    background: var(--backdrop);
    font-family: var(--font);
  }
  .card {
    position: absolute;
    left: 72px;
    top: 326px;
    width: 960px;
    height: 548px;
    background: var(--card);
  }
  .brand-mark {
    position: absolute;
    left: 244px;
    top: 175px;
    width: 118px;
    height: 118px;
    border-radius: 50%;
    background: var(--gold);
  }
  .brand-name {
    position: absolute;
    left: 0;
    width: 509px;
    top: 318px;
    text-align: center;
    font-size: 50px;
    font-weight: 400;
    color: var(--gold);
    letter-spacing: 0.5px;
  }
  .divider {
    position: absolute;
    left: 509px;
    top: 131px;
    width: 2px;
    height: 297px;
    background: var(--rule);
  }
  .details {
    position: absolute;
    left: 563px;
    top: 136px;
  }
  .person-name {
    font-size: 34px;
    font-weight: 700;
    color: var(--gold);
    line-height: 38px;
  }
  .person-title {
    font-size: 26px;
    color: var(--crimson);
    line-height: 32px;
  }
  .locations {
    margin-top: 18px;
    font-size: 26px;
    color: var(--ink);
    line-height: 34px;
  }
  .contact-list {
    list-style: none;
    margin-top: 8px;
  }
  .contact-item {
    display: flex;
    align-items: center;
    font-size: 25px;
    color: var(--ink);
    line-height: 37px;
  }
  .contact-icon {
    width: 22px;
    height: 22px;
    margin: 0 17px 0 6px;
    fill: var(--gold);
    flex: none;
  }
</style>
</head>
<body>
  <main class="card">
    <div class="brand-mark" aria-hidden="true"></div>
    <div class="brand-name">BrindlewayCare</div>

    <div class="divider" aria-hidden="true"></div>

    <section class="details">
      <h1 class="person-name">Derek Mallow</h1>
      <p class="person-title">Executive Chairman</p>
      <p class="locations">United Kingdom,<br>Australia, New Zealand</p>
      <ul class="contact-list">
        <li class="contact-item">
          <svg class="contact-icon" viewBox="0 0 24 24" aria-hidden="true">
            <path d="M6.6 10.8a15.1 15.1 0 0 0 6.6 6.6l2.2-2.2a1 1 0 0 1 1-.25 11.4 11.4 0 0 0 3.6.57 1 1 0 0 1 1 1V20a1 1 0 0 1-1 1A17 17 0 0 1 3 4a1 1 0 0 1 1-1h3.5a1 1 0 0 1 1 1c0 1.25.2 2.45.57 3.57a1 1 0 0 1-.25 1z"/>
          </svg>
          01742 918576
        </li>
        <li class="contact-item">
          <svg class="contact-icon" viewBox="0 0 24 24" aria-hidden="true">
            <path d="M2 5h20v2l-10 6L2 7z"/>
            <path d="M2 9l10 6 10-6v10H2z"/>
          </svg>
          d.mallow@plumvora.example
        </li>
        <li class="contact-item">
          <svg class="contact-icon" viewBox="0 0 24 24" aria-hidden="true">
            <path d="M12 2a10 10 0 1 0 0 20 10 10 0 0 0 0-20zm-1 17.9A8 8 0 0 1 4.1 11H7c.2 2.4 1.5 5.2 4 8.9zM7 9H4.3A8 8 0 0 1 11 4.1C8.6 6.6 7.3 8 7 9zm2 2h6c-.2 2-1.2 4.3-3 7-1.8-2.7-2.8-5-3-7zm0-2c.3-1.5 1.3-3 3-5 1.7 2 2.7 3.5 3 5zm4 10.9c2.5-3.7 3.8-6.5 4-8.9h2.9a8 8 0 0 1-6.9 8.9zM17 9c-.3-1-1.6-2.4-4-4.9A8 8 0 0 1 19.7 9z"/>
          </svg>
          www.plumvora.example
        </li>
      </ul>
    </section>
  </main>
</body>
</html>
```